Vorlanta PowerPoint Template

I have a company called Vorlanta, LLC and my company logo is already designed. I need a PowerPoint template that I will be using to pitch potential investors and business partners. This should be a very professional-looking template that leverages the company logo colors and really pops. The company is an AI product research and development company.

```html
<!DOCTYPE html>
<html lang="en">
<head>
<meta charset="utf-8">
<title>Vorlanta Presentation Template</title>
<link href="https://fonts.googleapis.com/css2?family=Poppins:wght@400;500;600;700&family=Roboto:wght@400;500&display=swap" rel="stylesheet">
<style>
:root{
  --red:#c1272d;
  --bright-red:#ff0000;
  --ink:#1f1f1f;
  --dark:#232323;
  --grey:#4a4a4a;
  --mid-grey:#7a7a7a;
  --text:#3a3a3a;
  --canvas:#eeeeee;
  --white:#ffffff;
}
*{box-sizing:border-box;margin:0;padding:0}
html,body{width:1105px;height:1200px;overflow:hidden;background:var(--canvas)}
body{position:relative;font-family:"Poppins",sans-serif;color:var(--text)}
.slide{position:absolute;width:804px;height:452px;background:var(--white);overflow:hidden;transform:scale(0.598);transform-origin:0 0}
.abs{position:absolute}
.rule{position:absolute;height:5px;width:50px;background:var(--mid-grey)}
.rule.light{background:var(--white)}
.heading{font-weight:700;font-size:36px;color:var(--ink);line-height:1.1}
.footer{position:absolute;left:0;top:420px;width:804px;height:26px;background:var(--ink);display:flex;align-items:center;padding:0 8px}
.footer .mark{width:15px;height:15px;border-radius:50%;background:var(--red);margin-right:6px}
.footer .name{color:var(--white);font-weight:600;font-size:16px;letter-spacing:-0.3px}
.footer .page{position:absolute;right:8px;top:2px;width:22px;height:22px;border-radius:50%;background:var(--white);border:2px solid var(--ink);box-shadow:0 0 0 1px var(--white);font-size:11px;font-weight:600;color:var(--ink);display:flex;align-items:center;justify-content:center}
.photo{position:absolute}
/* title */
.title-brand{position:absolute;left:28px;top:108px;display:flex;align-items:center}
.title-brand .mark{width:72px;height:72px;border-radius:50%;background:var(--red);margin-right:16px}
.title-brand .name{font-weight:600;font-size:60px;color:var(--red);letter-spacing:-2px}
.title-main{position:absolute;left:24px;top:212px;font-weight:700;font-size:38px;color:var(--ink)}
.title-sub{position:absolute;left:24px;top:266px;width:340px;font-family:"Roboto",sans-serif;font-size:19px;line-height:27px;color:var(--ink)}
/* agenda */
.agenda-item{position:absolute;display:flex;align-items:center;font-weight:500;font-size:15px;color:var(--ink)}
.agenda-item .num{width:36px;height:36px;border-radius:50%;background:var(--red);color:var(--white);font-weight:600;font-size:14px;display:flex;align-items:center;justify-content:center;margin-right:16px;flex:none}
/* about */
.about-band{position:absolute;left:242px;top:0;width:562px;height:220px;background:var(--red)}
.about-copy{position:absolute;left:327px;top:100px;width:440px;color:var(--white);font-size:14px;line-height:23.5px}
.col-head{position:absolute;font-weight:700;font-size:17px;color:var(--red)}
.col-copy{position:absolute;width:215px;font-size:12.5px;line-height:23px;color:var(--text)}
/* services */
.centered{position:absolute;left:0;width:804px;text-align:center}
.service{position:absolute;top:162px;width:239px;height:229px;border-radius:6px;color:var(--white);text-align:center;padding-top:20px}
.service svg{display:block;margin:0 auto}
.service h3{font-weight:700;font-size:19px;margin-top:12px}
.service p{font-size:13.5px;line-height:23px;margin-top:6px;padding:0 18px}
/* team */
.team-top{position:absolute;left:0;top:0;width:804px;height:226px;background:var(--grey)}
.member{position:absolute;top:168px;width:150px;text-align:center}
.member .pic{width:116px;height:116px;border-radius:50%;margin:0 auto;border:3px solid var(--white);background:linear-gradient(160deg,#c8d2dc,#4d5d70 70%,#2a3340)}
.member h4{font-weight:700;font-size:14px;color:var(--red);margin-top:14px}
.member p{font-size:10.5px;line-height:13.5px;color:var(--text);margin-top:4px;padding:0 14px}
/* graph */
.graph-copy{position:absolute;left:412px;width:370px;font-size:13.5px;line-height:22.5px;color:var(--text)}
.graph-sub{position:absolute;left:412px;font-weight:700;font-size:17px;color:var(--red)}
/* thanks */
.thanks-brand{position:absolute;left:181px;top:48px;display:flex;align-items:center}
.thanks-brand .mark{width:96px;height:96px;border-radius:50%;background:var(--red);margin-right:22px}
.thanks-brand .name{font-weight:600;font-size:80px;color:var(--white);letter-spacing:-3px}
.social{position:absolute;top:352px;width:36px;height:36px;border-radius:50%;border:2px solid var(--white)}
</style>
</head>
<body>

<!-- 1 Title -->
<section class="slide" style="left:48.4px;top:27.5px">
  <svg class="abs" style="left:0;top:0" width="804" height="452" aria-hidden="true">
    <path d="M600 0H804V452H600Q520 226 600 0Z" fill="var(--red)"/>
  </svg>
  <div class="photo" role="img" aria-label="Photo of a team meeting around a laptop in a modern office" style="left:401px;top:31px;width:390px;height:390px;border-radius:50%;background:radial-gradient(circle at 40% 40%,#9fb3c4,#3d5468 55%,#1b2633)"></div>
  <div class="title-brand"><span class="mark"></span><span class="name">Vorlanta</span></div>
  <h1 class="title-main">Title Presentation</h1>
  <p class="title-sub">Excepteur sint occaecat cupidatat non proident, sunt in culpa qui officia deserunt</p>
</section>

<!-- 5 Team -->
<section class="slide" style="left:577.6px;top:27.5px">
  <div class="team-top"></div>
  <div class="rule light" style="left:377px;top:30px;width:50px"></div>
  <h2 class="centered heading" style="top:44px;color:var(--white)">Meet Our Teams</h2>
  <p class="centered" style="top:104px;font-size:11px;line-height:19px;color:var(--white)">Sed ut perspiciatis unde omnis iste natus error sit voluptatem accusanti um doloremque laudantium,<br>totam rem aperiam, eaque ipsa quae ab illo inventore veritatis et quasi.</p>
  <div class="member" style="left:5px"><div class="pic" role="img" aria-label="Portrait of a team member"></div><h4>Name Heading</h4><p>Excepteur sint occa ecat cupidatat non proident</p></div>
  <div class="member" style="left:166px"><div class="pic" role="img" aria-label="Portrait of a team member"></div><h4>Name Heading</h4><p>Excepteur sint occa ecat cupidatat non proident</p></div>
  <div class="member" style="left:327px"><div class="pic" role="img" aria-label="Portrait of a team member"></div><h4>Name Heading</h4><p>Excepteur sint occa ecat cupidatat non proident</p></div>
  <div class="member" style="left:488px"><div class="pic" role="img" aria-label="Portrait of a team member"></div><h4>Name Heading</h4><p>Excepteur sint occa ecat cupidatat non proident</p></div>
  <div class="member" style="left:649px"><div class="pic" role="img" aria-label="Portrait of a team member"></div><h4>Name Heading</h4><p>Excepteur sint occa ecat cupidatat non proident</p></div>
  <footer class="footer"><span class="mark"></span><span class="name">Vorlanta</span><span class="page">5</span></footer>
</section>

<!-- 2 Agenda -->
<section class="slide" style="left:48.4px;top:311px">
  <svg class="abs" style="left:0;top:0" width="804" height="452" role="img" aria-label="Photo of two colleagues presenting at a whiteboard">
    <defs><linearGradient id="agendaPhoto" x1="0" y1="0" x2="1" y2="1"><stop offset="0" stop-color="#b9c7d3"/><stop offset="0.6" stop-color="#566b80"/><stop offset="1" stop-color="#1f2c3a"/></linearGradient></defs>
    <path d="M0 0H358Q465 70 395 250Q330 390 170 404H0Z" fill="url(#agendaPhoto)"/>
    <path d="M358 0Q465 70 395 250Q330 390 170 404" fill="none" stroke="var(--ink)" stroke-width="6"/>
  </svg>
  <div class="rule" style="left:443px;top:46px"></div>
  <h2 class="heading abs" style="left:443px;top:60px">Agenda</h2>
  <div class="agenda-item" style="left:433px;top:128px"><span class="num">1</span>Duis aute irure dolor</div>
  <div class="agenda-item" style="left:416px;top:182px"><span class="num">2</span>Reprehenderit in voluptate</div>
  <div class="agenda-item" style="left:388px;top:235px"><span class="num">3</span>Velit esse cillum</div>
  <div class="agenda-item" style="left:354px;top:288px"><span class="num">4</span>Dolore eu fugiat nulla pariatur</div>
  <div class="agenda-item" style="left:302px;top:342px"><span class="num">5</span>Duis aute irure dolor</div>
  <footer class="footer"><span class="mark"></span><span class="name">Vorlanta</span><span class="page">2</span></footer>
</section>

<!-- 6 Content break -->
<section class="slide" style="left:577.6px;top:311px">
  <div class="photo" role="img" aria-label="Red-toned photo of a presenter and colleague in a technology setting" style="left:0;top:0;width:804px;height:452px;background:linear-gradient(100deg,#1a0405 0%,#7a0f12 30%,#d01c1f 45%,#5a0a0c 62%,#a8161a 80%,#2a0607 100%)"></div>
  <div class="rule light" style="left:377px;top:183px"></div>
  <h2 class="centered heading" style="top:200px;color:var(--white);line-height:38px">Content Break Slide<br>Goes Here</h2>
</section>

<!-- 3 About -->
<section class="slide" style="left:48.4px;top:597px">
  <div class="about-band"></div>
  <div class="photo" role="img" aria-label="Photo of business people using phones and tablets with a network graphic" style="left:16px;top:24px;width:278px;height:382px;background:linear-gradient(160deg,#8d9aa6,#3d4650 50%,#5b4633 100%)"></div>
  <div class="rule light" style="left:327px;top:28px"></div>
  <h2 class="heading abs" style="left:327px;top:44px;color:var(--white)">About Vorlanta</h2>
  <p class="about-copy">Duis aute irure dolor in reprehenderit in voluptate velit esse cillum dolore eu fugiat nulla pariatur. Excepteur sint occaecat cupidatat non proident, sunt in culpa qui officia deserunt mollit anim id est laborum</p>
  <h3 class="col-head" style="left:316px;top:236px">Mission</h3>
  <p class="col-copy" style="left:316px;top:266px">Dolor in reprehenderit in voluptate velit esse cillumdolore eu fugiat nulla pariaturpeteur sint occaecat cupidatat non proident, sunt in culpa qui officia deserunt mollit.</p>
  <h3 class="col-head" style="left:568px;top:236px">Mission</h3>
  <p class="col-copy" style="left:568px;top:266px">Dolor in reprehenderit in voluptate velit esse cillumdolore eu fugiat nulla pariaturpeteur sint occaecat cupidatat non proident, sunt in culpa qui officia deserunt mollit.</p>
  <footer class="footer"><span class="mark"></span><span class="name">Vorlanta</span><span class="page">3</span></footer>
</section>

<!-- 7 Graph -->
<section class="slide" style="left:577.6px;top:597px">
  <svg class="abs" style="left:0;top:0" width="400" height="410" role="img" aria-label="Bar chart comparing two series from 2019 to 2025">
    <g font-family="Poppins, sans-serif" font-size="7" fill="#333" text-anchor="end">
      <text x="30" y="112">100%</text><text x="30" y="139">90%</text><text x="30" y="166">80%</text><text x="30" y="194">70%</text><text x="30" y="221">60%</text><text x="30" y="248">50%</text><text x="30" y="275">40%</text><text x="30" y="302">30%</text><text x="30" y="330">20%</text><text x="30" y="357">10%</text><text x="30" y="384">0%</text>
    </g>
    <line x1="40" y1="382" x2="392" y2="382" stroke="#ccc"/>
    <g fill="var(--ink)">
      <rect x="48" y="205" width="15" height="177"/><rect x="97" y="232" width="15" height="150"/><rect x="146" y="137" width="15" height="245"/><rect x="194" y="241" width="15" height="141"/><rect x="243" y="295" width="15" height="87"/><rect x="292" y="175" width="15" height="207"/><rect x="341" y="113" width="15" height="269"/>
    </g>
    <g fill="var(--red)">
      <rect x="63" y="273" width="15" height="109"/><rect x="112" y="162" width="15" height="220"/><rect x="161" y="319" width="15" height="63"/><rect x="209" y="273" width="15" height="109"/><rect x="258" y="249" width="15" height="133"/><rect x="307" y="205" width="15" height="177"/><rect x="356" y="352" width="15" height="30"/>
    </g>
    <g font-family="Poppins, sans-serif" font-size="7" fill="#333" text-anchor="middle">
      <text x="63" y="399">2019</text><text x="112" y="399">2020</text><text x="161" y="399">2021</text><text x="209" y="399">2022</text><text x="258" y="399">2023</text><text x="307" y="399">2024</text><text x="356" y="399">2025</text>
    </g>
  </svg>
  <div class="rule" style="left:412px;top:38px"></div>
  <h2 class="heading abs" style="left:411px;top:54px">Graph Content Slide</h2>
  <p class="graph-copy" style="top:100px">Duis aute irure dolor in reprehenderit in voluptate velit esse cillum dolore eu fugiat nullapariatur occaecat cupidatat non proident</p>
  <h3 class="graph-sub" style="top:184px">Duis aute irure</h3>
  <p class="graph-copy" style="top:211px;font-size:12.5px">Dolor in reprehenderit in voluptate velit esse cillum dolore eu fugiat nulla pariaturepteur sint occaecat cupidatat non proident, sunt in culpa.</p>
  <h3 class="graph-sub" style="top:295px">Duis aute irure</h3>
  <p class="graph-copy" style="top:322px;font-size:12.5px">Dolor in reprehenderit in voluptate velit esse cillum dolore eu fugiat nulla pariaturepteur sint occaecat cupidatat non proident, sunt in culpa.</p>
  <footer class="footer"><span class="mark"></span><span class="name">Vorlanta</span><span class="page">7</span></footer>
</section>

<!-- 4 Services -->
<section class="slide" style="left:48.4px;top:883px">
  <div class="rule" style="left:377px;top:30px"></div>
  <h2 class="centered heading" style="top:44px;color:var(--grey)">Services</h2>
  <p class="centered" style="top:94px;font-size:14px;line-height:24px;color:var(--text)">Duis aute irure dolor in reprehenderit in voluptate velit esse cillum dolore eu fugiat nulla pariatur.<br>Excepteur sint occaecat cupidatat non proident, sunt in culpa qui officia deserunt</p>
  <div class="service" style="left:22px;background:var(--red)">
    <svg width="48" height="48" viewBox="0 0 48 48" fill="none" stroke="#fff" stroke-width="2" aria-hidden="true"><rect x="6" y="4" width="28" height="38" rx="2"/><circle cx="22" cy="24" r="8"/><line x1="28" y1="30" x2="40" y2="42"/><line x1="12" y1="10" x2="28" y2="10"/></svg>
    <h3>Dolore Magna</h3><p>Dolor in reprehenderit in voluptate velit esse cillum dolore eu fugiat nulla paria turepteur sint occa.</p>
  </div>
  <div class="service" style="left:282px;background:var(--grey)">
    <svg width="48" height="48" viewBox="0 0 48 48" fill="none" stroke="#fff" stroke-width="2" aria-hidden="true"><circle cx="24" cy="24" r="20"/><circle cx="24" cy="24" r="11"/><text x="24" y="28" text-anchor="middle" font-family="Poppins, sans-serif" font-size="11" fill="#fff" stroke="none">AI</text></svg>
    <h3>Dolore Magna</h3><p>Dolor in reprehenderit in voluptate velit esse cillum dolore eu fugiat nulla paria turepteur sint occa.</p>
  </div>
  <div class="service" style="left:542px;background:var(--bright-red)">
    <svg width="48" height="48" viewBox="0 0 48 48" fill="none" stroke="#fff" stroke-width="2" aria-hidden="true"><rect x="4" y="8" width="40" height="30" rx="2"/><line x1="4" y1="14" x2="44" y2="14"/><circle cx="26" cy="25" r="6"/><line x1="30" y1="29" x2="36" y2="35"/><line x1="9" y1="20" x2="17" y2="20"/><line x1="9" y1="26" x2="17" y2="26"/></svg>
    <h3>Dolore Magna</h3><p>Dolor in reprehenderit in voluptate velit esse cillum dolore eu fugiat nulla paria turepteur sint occa.</p>
  </div>
  <footer class="footer"><span class="mark"></span><span class="name">Vorlanta</span><span class="page">4</span></footer>
</section>

<!-- 8 Thank you -->
<section class="slide" style="left:577.6px;top:883px;background:var(--dark)">
  <div class="photo" role="img" aria-label="Dark photo of a person in profile with technology graphics" style="left:0;top:0;width:804px;height:452px;background:linear-gradient(90deg,#141a22 0%,#24303c 40%,#1a1e24 70%,#0d0d0f 100%)"></div>
  <div class="thanks-brand"><span class="mark"></span><span class="name">Vorlanta</span></div>
  <div class="rule light" style="left:377px;top:196px"></div>
  <h2 class="centered heading" style="top:214px;color:var(--white)">Thank You</h2>
  <p class="centered" style="top:274px;font-size:15px;line-height:29px;color:var(--white)">Lorem ipsum dolor sit amet, consectetur adipiscing elit, sed do eiusmod tempor incididunt ut<br>labore et dolore magna aliquanim ad minim veniam, quis nostrud exercitation ullamco.</p>
  <span class="social" style="left:320px"></span>
  <span class="social" style="left:383px"></span>
  <span class="social" style="left:450px"></span>
</section>

</body>
</html>
```